Lantern Petals Website v.1 - attract floral shop franchisees

I need a simple information website for my new business. We are a franchisor of flower shops. The overall purpose of the website is to promote the company and the service, especially to potential franchisees and retailers. Only about 4 pages are required including homepage, About, For Supermarkets, For Franchisees, and Contact. No special functions are required except the site will have two separate inquiry forms that must be filled out online and submitted via automated email. Similarly, an email form should be linked from the Contact page. I have a logo and business cards designed by ArtMingle, and I would like the site to have a consistent color scheme and style. The key to design will be to express the joy and love associated with flowers and floral bouquets.
IMPORTANT - I will be exporting the website design to Wordpress CMS in a site hosted by HostNimbus. For smooth integration into WordPress hosted by HostNimbus, the designer should build the site using a WordPress-friendly format. Ideally, they should use HTML, CSS, and PHP. Creating a custom theme or using a page builder that exports to WordPress-compatible files is best. This ensures the site can be easily imported and managed within WordPress.

Target Market(s)

Potential franchisees (existing florists or creative types who might like to own a floral business) and supermarkets who might want us to run their floral department

Industry/Entity Type

Floral retailing

Requirements
Must have
• A brand theme that is beautiful, consistent throughout and builds on the logo design
Nice to have
• Show gender and ethnic diversity in customers and florists. Pictures of happy florists (for franchisees) and pictures of amazing floral department displays (for supermarkets)

```html
<!DOCTYPE html>
<html lang="en">
<head>
<meta charset="utf-8">
<title>Lantern Petals</title>
<link href="https://fonts.googleapis.com/css2?family=Arimo:wght@400;700&family=Dancing+Script:wght@400&display=swap" rel="stylesheet">
<style>
:root{
  --green:#1a9146;
  --orange:#f29d1d;
  --ink:#3d3d3d;
  --muted:#555;
  --cream:#f2f1e3;
  --dark:#1b1b1b;
  --white:#fff;
}
*{box-sizing:border-box;margin:0;padding:0}
html,body{width:1200px;height:3118px;overflow:hidden}
body{position:relative;font-family:'Arimo',Arial,sans-serif;color:var(--ink);background:var(--white)}
.abs{position:absolute}
.topbar{left:0;top:0;width:1200px;height:22px;background:var(--green);color:var(--white);font-size:11px;text-align:center;line-height:22px}
.header{left:0;top:22px;width:1200px;height:77px;background:var(--white)}
.brand{left:121px;top:22px;display:flex;align-items:center;gap:8px}
.brand-dot{width:22px;height:22px;border-radius:50%;background:var(--orange)}
.brand-name{font-size:20px;color:var(--orange);font-weight:400}
.nav{top:31px;font-size:11.5px;color:var(--ink)}
.search{left:773px;top:19px;width:175px;height:36px;border:1px solid #333;border-radius:18px;padding-left:12px;font-size:11.5px;line-height:34px}
.search svg{position:absolute;right:10px;top:8px}
.util{top:30px;font-size:11.5px;display:flex;align-items:center;gap:5px}
.hero{left:0;top:99px;width:1200px;height:556px;background:radial-gradient(ellipse at 30% 30%,#a9892f 0%,#5e5a2a 35%,#2c3320 70%,#1d2418 100%)}
.hero-art{position:absolute;inset:0;background:linear-gradient(90deg,rgba(180,60,40,.25) 0%,rgba(0,0,0,0) 40%,rgba(240,170,30,.35) 100%)}
.hero-title{left:0;top:330px;width:1200px;text-align:center;color:var(--white);font-size:41px;line-height:46px}
.hero-sub{left:0;top:430px;width:1200px;text-align:center;color:var(--white);font-size:13px;line-height:18px}
.label{font-family:'Dancing Script',cursive;font-size:17px;color:var(--orange);display:flex;align-items:center;gap:8px}
.label::after{content:"";display:block;width:70px;height:1px;background:var(--orange)}
.heading{font-size:27px;color:var(--ink)}
.copy{font-size:9.8px;line-height:15px;color:var(--muted)}
.btn{background:var(--orange);color:var(--white);font-size:11px;border-radius:17px;text-align:center;line-height:33px;height:33px}
.ring{border-radius:50%}
.photo{border-radius:50%}
.supermarkets{left:0;top:1114px;width:1200px;height:458px;background:linear-gradient(180deg,#4a4d48 0%,#39402f 30%,#2b3a25 60%,#3b2d22 100%)}
.gallery{left:0;top:2025px;width:1200px;height:639px;background:var(--cream)}
.g-label{justify-content:center}
.g-label::before{content:"";display:block;width:70px;height:1px;background:var(--orange)}
.tile{border-radius:2px}
.cta{left:0;top:2664px;width:1200px;height:222px;background:var(--orange)}
.cta-title{left:0;top:2726px;width:1200px;text-align:center;color:var(--white);font-size:28px}
.cta-field{left:343px;top:2773px;width:513px;height:40px;border-radius:20px;background:var(--cream);border:2px solid var(--white);font-size:11px;padding-left:14px;line-height:36px;color:var(--ink)}
.cta-btn{left:730px;top:2776px;width:124px;height:34px;border-radius:17px;background:var(--green);color:var(--white);font-size:11px;text-align:center;line-height:34px}
.footer{left:0;top:2886px;width:1200px;height:232px;background:var(--dark);color:var(--white)}
.vline{width:1px;height:156px;top:2916px;background:#777}
.f-head{font-size:17px;color:var(--white)}
.f-text{font-size:9px;line-height:14.5px;color:#e8e8e8}
.f-links{font-size:9px;line-height:19.4px;color:#e8e8e8;list-style:none}
.f-contact{font-size:9px;display:flex;align-items:center;gap:7px;color:#e8e8e8}
.icon-circle{width:20px;height:20px;border-radius:50%;border:1px solid #ddd;display:flex;align-items:center;justify-content:center}
.hline{left:121px;top:3072px;width:957px;height:1px;background:#777}
.copyright{left:0;top:3082px;width:1200px;text-align:center;font-size:9px;color:#e8e8e8}
</style>
</head>
<body>

<div class="abs topbar">Welcome to Lantern Petals is an entrepreneurial company</div>

<header class="abs header">
  <div class="abs brand"><span class="brand-dot"></span><span class="brand-name">Lantern Petals</span></div>
  <span class="abs nav" style="left:297px">About Us</span>
  <span class="abs nav" style="left:374px">For Supermarkets</span>
  <span class="abs nav" style="left:496px">For Franchisees</span>
  <span class="abs nav" style="left:608px">Our Gallery</span>
  <span class="abs nav" style="left:697px">Contact Us</span>
  <div class="abs search">Search
    <svg width="18" height="18" viewBox="0 0 18 18"><circle cx="7.5" cy="7.5" r="6" fill="none" stroke="#333" stroke-width="1.6"/><line x1="12" y1="12" x2="17" y2="17" stroke="#333" stroke-width="1.8"/></svg>
  </div>
  <div class="abs util" style="left:965px">
    <svg width="14" height="14" viewBox="0 0 14 14"><circle cx="7" cy="7" r="7" fill="var(--green)"/><text x="7" y="10.5" font-size="10" text-anchor="middle" fill="#fff" font-family="Arimo">?</text></svg>Help
  </div>
  <div class="abs util" style="left:1022px">
    <svg width="16" height="14" viewBox="0 0 16 14"><circle cx="6" cy="4" r="3.5" fill="var(--green)"/><path d="M0 14c0-4 2.5-6 6-6s6 2 6 6z" fill="var(--green)"/><path d="M13 3v5M10.5 5.5h5" stroke="var(--green)" stroke-width="1.6"/></svg>Sign In
  </div>
</header>

<section class="abs hero" role="img" aria-label="Close-up photo of a mixed bouquet of orange and yellow flowers">
  <div class="hero-art"></div>
</section>
<h1 class="abs hero-title" style="font-weight:400">Lantern Petals is<br>an entrepreneurial company</h1>
<p class="abs hero-sub">Created to make top quality fresh flowers and artisan-designed bouquets<br>accessible to every consumer at affordable prices.</p>

<!-- About -->
<div class="abs ring" style="left:185px;top:705px;width:358px;height:358px;background:var(--green)"></div>
<div class="abs photo" role="img" aria-label="Photo of a smiling florist holding fresh bouquets" style="left:210px;top:718px;width:333px;height:333px;background:linear-gradient(160deg,#d8dcc8 0%,#a9a89a 45%,#e0c94a 75%,#c78a4a 100%);border:3px solid #fff"></div>
<div class="abs label" style="left:714px;top:741px">About Us</div>
<h2 class="abs heading" style="left:714px;top:769px;font-weight:400">About Lantern Petals</h2>
<p class="abs copy" style="left:714px;top:812px;width:370px">Fresh flowers convey special sentiments - love, happiness, joy – which every person deserves.&nbsp; Lantern Petals is an entrepreneurial company created to make top quality fresh flowers and artisan-designed bouquets accessible to every consumer at affordable prices.<br><br>Lantern Petals brings the best of professional florists and supermarkets together for the benefit of consumers.&nbsp; It supports a national network of franchisees who own and operate the floral departments of some of the country's most progressive supermarkets, selling the finest floral stems and bouquets to customers at the market's best value.</p>
<div class="abs btn" style="left:714px;top:978px;width:106px">More About Us</div>

<!-- Supermarkets -->
<section class="abs supermarkets" role="img" aria-label="Photo of a greenhouse filled with rows of red gerbera flowers"></section>
<div class="abs label" style="left:122px;top:1220px">Supermarkets</div>
<h2 class="abs heading" style="left:122px;top:1247px;color:#fff;font-weight:400">For Supermarkets</h2>
<p class="abs copy" style="left:122px;top:1289px;width:392px;color:#fff">Supermarket flower departments benefit from high customer footfall, economies of scale and low pricing.&nbsp; However their quality of stems and bouquets is often poor and in-store service is limited.&nbsp; In contrast, professional florists typically sell the finest quality stems, design the most beautiful bouquets and provide the finest customer service, but their costs and customer prices are high.&nbsp; Supermarkets find that Lantern Petals, through their florist franchise network, is able to improve their financial outcomes, provide attentive customer service and satisfaction, and lift the quality of the entire store environment.</p>
<div class="abs btn" style="left:122px;top:1424px;width:155px">More For Supermarkets</div>
<div class="abs ring" style="left:640px;top:1164px;width:362px;height:362px;background:var(--orange)"></div>
<div class="abs photo" role="img" aria-label="Photo of a bouquet of white hydrangeas and pink roses" style="left:642px;top:1176px;width:336px;height:336px;background:linear-gradient(150deg,#eef0ea 0%,#cfd6c6 35%,#d2457a 65%,#3f6b35 100%);border:3px solid #fff"></div>

<!-- Franchisees -->
<div class="abs ring" style="left:185px;top:1622px;width:358px;height:358px;background:var(--green)"></div>
<div class="abs photo" role="img" aria-label="Photo of vases filled with pink and red mixed flowers" style="left:210px;top:1635px;width:333px;height:333px;background:linear-gradient(160deg,#c8c6bc 0%,#d9779b 40%,#c0435e 65%,#7a5a3a 100%);border:3px solid #fff"></div>
<div class="abs label" style="left:714px;top:1663px">Franchisees</div>
<h2 class="abs heading" style="left:714px;top:1689px;font-weight:400">About Lantern Petals</h2>
<p class="abs copy" style="left:714px;top:1732px;width:370px">Lantern Petals supports a national network of owner-operator franchisees with comprehensive services to enhance franchise profits.&nbsp; Our franchisees are the cornerstone of our business.&nbsp; Many of them are already professional florists or florist employees who wish to expand their businesses without the significant costs of a traditional flower shop.&nbsp; Others are creative types or flower lovers who have made a career change in order to express their talents and make people happy.&nbsp; Still others are entrepreneurs in search of owning their own business.&nbsp; All are welcome if they meet Lantern Petals' high standards of quality, service and ethical Business practices.</p>
<div class="abs btn" style="left:714px;top:1899px;width:143px">More For Franchisees</div>

<!-- Gallery -->
<section class="abs gallery"></section>
<div class="abs label g-label" style="left:0;top:2063px;width:1200px">Our Gallery</div>
<h2 class="abs heading" style="left:0;top:2087px;width:1200px;text-align:center;font-weight:400">Our Gallery</h2>
<div class="abs tile" role="img" aria-label="Photo of hydrangeas and pink roses" style="left:122px;top:2143px;width:279px;height:194px;background:linear-gradient(150deg,#f1f1ec 0%,#cf4b7e 60%,#3d6b34 100%)"></div>
<div class="abs tile" role="img" aria-label="Photo of orange pincushion proteas and yellow blooms" style="left:413px;top:2143px;width:278px;height:194px;background:linear-gradient(150deg,#c0552a 0%,#f0a42a 50%,#5a6a4a 100%)"></div>
<div class="abs tile" role="img" aria-label="Photo of a florist's table with yellow roses and hydrangeas" style="left:122px;top:2349px;width:279px;height:194px;background:linear-gradient(150deg,#b7b9a6 0%,#e5cf45 45%,#c7d3e0 75%,#6d6a60 100%)"></div>
<div class="abs tile" role="img" aria-label="Photo of vases of pink mixed flowers" style="left:413px;top:2349px;width:278px;height:194px;background:linear-gradient(150deg,#d9779b 0%,#c0435e 55%,#8a5a3a 100%)"></div>
<div class="abs tile" role="img" aria-label="Photo of a greenhouse with rows of red gerberas" style="left:702px;top:2143px;width:376px;height:402px;background:linear-gradient(180deg,#d9dcd6 0%,#9aa19a 35%,#3d5a33 65%,#2d3d27 100%)"></div>
<div class="abs btn" style="left:538px;top:2573px;width:123px">More Our Gallery</div>

<!-- CTA -->
<section class="abs cta"></section>
<h2 class="abs cta-title" style="font-weight:400">Start Your New Journey Lantern Petals</h2>
<div class="abs cta-field">Enter Your Email</div>
<div class="abs cta-btn">More Our Gallery</div>

<!-- Footer -->
<footer class="abs footer"></footer>
<div class="abs brand" style="top:2950px;left:125px"><span class="brand-dot"></span><span class="brand-name" style="font-size:24px">Lantern Petals</span></div>
<div class="abs vline" style="left:363px"></div>
<div class="abs vline" style="left:653px"></div>
<div class="abs vline" style="left:878px"></div>
<h3 class="abs f-head" style="left:410px;top:2912px;font-weight:400">About Us</h3>
<p class="abs f-text" style="left:410px;top:2948px;width:205px">Fresh flowers convey special sentiments - love, happiness, joy – which every person deserves. Lantern Petals is an entrepreneurial company created to make top quality fresh flowers and artisan-designed bouquets accessible to every consumer at affordable prices.</p>
<h3 class="abs f-head" style="left:724px;top:2912px;font-weight:400">Quick Link</h3>
<ul class="abs f-links" style="left:727px;top:2944px">
  <li>Home</li><li>About Us</li><li>For Supermarkets</li><li>For Franchisees</li><li>Our Gallery</li><li>Contact Us</li>
</ul>
<h3 class="abs f-head" style="left:937px;top:2912px;font-weight:400">Contact Us</h3>
<div class="abs f-contact" style="left:937px;top:2946px">
  <span class="icon-circle"><svg width="11" height="8" viewBox="0 0 11 8"><rect x=".5" y=".5" width="10" height="7" fill="none" stroke="#fff"/><path d="M.5 .5l5 4 5-4" fill="none" stroke="#fff"/></svg></span>mia@lantern-petals.com
</div>
<div class="abs f-contact" style="left:937px;top:2980px">
  <span class="icon-circle"><svg width="10" height="10" viewBox="0 0 10 10"><path d="M2 0.5l2 2.5-1.2 1.2c.6 1.3 1.6 2.3 2.9 2.9L7 5.9l2.5 2-1.3 1.6C4.5 9.5.5 5.5.5 1.8z" fill="#fff"/></svg></span>+1.555.014.2277
</div>
<div class="abs hline"></div>
<p class="abs copyright">Copyright © 2024 Lantern Petals All Rights Reserved.</p>

</body>
</html>
```